Business Card Design - Amberfield Court

We are looking at a new design for our business cards that has a modern and professional look. We run a residential aged care facility focussing on the care of residents. The cards will be used for potential clients, consultants and business opportunities in this sector. Blue and white is our main colours and would to see these colours incorporated in the design.
Industry/Entity Type
Business
Contact Information for Business Card
Amberfield Court, Darren Walsh, dwalsh@amberfieldcourt.com.au, Finance Manager, 0472 639 208, BCom, 37 Marrabel Crescent, Brindle Vale, Qld 4093.
Look and feel
Each slider illustrates characteristics of the customer's brand and the style your logo design should communicate.

```html
<!DOCTYPE html>
<html lang="en">
<head>
<meta charset="utf-8">
<title>Amberfield Court – Business Card</title>
<link href="https://fonts.googleapis.com/css2?family=Source+Sans+3:ital,wght@0,400;0,600;1,400&display=swap" rel="stylesheet">
<style>
  :root {
    --backdrop: #eeeeee;
    --card-white: #f7f7f6;
    --brand-blue: #43687f;
    --name-blue: #3d6a88;
    --taupe: #9b928b;
    --title-grey: #8e8985;
    --text-grey: #4d4d4d;
    --rule-grey: #9a9a9a;
    --white: #ffffff;
  }
  * { margin: 0; padding: 0; box-sizing: border-box; }
  html, body { width: 1105px; height: 1200px; overflow: hidden; }
  body {
    background: var(--backdrop);
    font-family: "Source Sans 3", sans-serif;
    position: relative;
  }
  .card {
    position: absolute;
    left: 172px;
    width: 760px;
    height: 436px;
    overflow: hidden;
  }
  .card-front { top: 120px; background: var(--card-white); }
  .card-back { top: 640px; background: var(--brand-blue); }

  .front-brand {
    position: absolute;
    right: 38px;
    top: 150px;
    display: flex;
    align-items: center;
    gap: 14px;
  }
  .brand-dot {
    width: 26px; height: 26px;
    border-radius: 50%;
    background: var(--brand-blue);
  }
  .brand-name {
    font-weight: 600;
    font-size: 34px;
    color: var(--brand-blue);
    letter-spacing: 0.5px;
  }

  .holder-name {
    position: absolute;
    left: 38px; top: 258px;
    font-weight: 600;
    font-size: 28px;
    color: var(--name-blue);
  }
  .holder-name .credential { font-size: 21px; }
  .holder-title {
    position: absolute;
    left: 38px; top: 296px;
    font-size: 20px;
    color: var(--title-grey);
  }
  .title-rule {
    position: absolute;
    left: 206px; right: 38px; top: 310px;
    height: 1px;
    background: var(--rule-grey);
  }
  .contact-list {
    position: absolute;
    left: 38px; top: 332px;
    list-style: none;
    font-size: 20px;
    color: var(--text-grey);
    line-height: 30px;
  }
  .contact-list li { display: flex; align-items: center; gap: 10px; }
  .contact-list svg { width: 18px; height: 18px; fill: var(--brand-blue); }
  .address {
    position: absolute;
    right: 38px; top: 332px;
    font-style: normal;
    font-size: 20px;
    color: var(--text-grey);
    line-height: 30px;
    text-align: right;
  }
  .edge-band {
    position: absolute;
    left: 0; bottom: 0;
    width: 100%; height: 15px;
  }

  .back-brand {
    position: absolute;
    left: 0; right: 0; top: 178px;
    text-align: center;
    font-weight: 600;
    font-size: 48px;
    color: var(--white);
    letter-spacing: 1px;
  }
  .back-web {
    position: absolute;
    left: 0; right: 0; top: 288px;
    text-align: center;
    font-style: italic;
    font-size: 21px;
    color: var(--white);
    letter-spacing: 1.5px;
  }
</style>
</head>
<body>
  <section class="card card-front">
    <div class="front-brand">
      <span class="brand-dot"></span>
      <span class="brand-name">Amberfield Court</span>
    </div>

    <h1 class="holder-name">Darren Walsh <span class="credential">BCom</span></h1>
    <p class="holder-title">Finance Manager</p>
    <div class="title-rule"></div>

    <ul class="contact-list">
      <li>
        <svg viewBox="0 0 24 24" aria-hidden="true"><path d="M6.6 10.8a15.1 15.1 0 0 0 6.6 6.6l2.2-2.2a1 1 0 0 1 1-.25 11.4 11.4 0 0 0 3.6.57 1 1 0 0 1 1 1V20a1 1 0 0 1-1 1A17 17 0 0 1 3 4a1 1 0 0 1 1-1h3.5a1 1 0 0 1 1 1c0 1.25.2 2.45.57 3.57a1 1 0 0 1-.25 1z"/></svg>
        0472 639 208
      </li>
      <li>
        <svg viewBox="0 0 24 24" aria-hidden="true"><path d="M2 5h20v14H2zM4 7v.6l8 5 8-5V7l-8 5z"/></svg>
        dwalsh@amberfieldcourt.com.au
      </li>
    </ul>

    <address class="address">
      37 Marrabel Crescent<br>
      Brindle Vale, Qld 4093.
    </address>

    <svg class="edge-band" viewBox="0 0 760 15" preserveAspectRatio="none" aria-hidden="true">
      <polygon points="0,0 498,0 494,15 0,15" fill="var(--brand-blue)"/>
      <polygon points="502,0 760,0 760,15 498,15" fill="var(--taupe)"/>
    </svg>
  </section>

  <section class="card card-back">
    <p class="back-brand">Amberfield Court</p>
    <p class="back-web">www.amberfieldcourt.com.au</p>
  </section>
</body>
</html>
```